Business Name: DM Space Arranging Pty Ltd

Business Type: Professional Home Styling and Minor Renovation Business

Logo: Attached is the logo that has been created.
I always envisaged the logo in the middle of the business card with my full name underneath it.

Marnie Tulloch B.Com LMR HTV
Property Stylist & Project Manager

Include dot points of services
Staging Houses for Sale
Minor Home Renovations
Home Styling & Project Management
Re-Designing Living Spaces to Aid the Disabled

Somewhere on the card I would like to incorporate
"Property Styling and Cosmetic Renovations"

Colour Scheme:
Gloss black business card, with white and then
Gold or Silver as the highlight colours.

Incorporate a small amount of yellow only if possible to make it pop. If this really doesn’t work it doesn’t have to be used. Also l like the colour teal if that needs to be used as a contrast colour.

Feel/Themes
• I love antique chairs, regal expensive looking furniture mixed with modern homes (this is the unique style I want to sell) antique and modern mix that looks high class as well as modern and fresh, targeting an executive market.
• I want to use an orchid as a trademark throughout the course of my work, not sure if this can somehow be incorporated? Also really like crowns to give that regal/antique feel and then something else to give that modern twist (I don’t know what the something else could be)
• Wall Paper Look (on a portion of it not all of it, like a French look)
• Overall feel - A very deluxe and professional feel with a little bit of creative flare.

I hope this helps create a bit of a picture.

Is it ok that I call you tomorrow morning? My mobile number is 0438 926 574 if you have any questions for me in the meantime.

Target Market(s)

High Quality Executive Market - People selling homes

Industry/Entity Type

Business

Contact Information for Business Card

Include dot points of services:
Staging Houses for Sale
Minor Home Renovations

Font styles to use
Serif
Script

Colors
33b8a4
fbed22

Requirements
Must have
• Marnie Tulloch B.Com LMR HTV
• Property Stylist & Project Manager
• LMR and HTV Logos on the card
• "Dramatically increase the value of your property"
Nice to have
• Colour Scheme:
• Gloss black business card, with white and then
• Gold or Silver as the highlight colours.
• Incorporate a small amount of yellow only if possible to make it pop. If this really doesn’t work it doesn’t have to be used. Also l like the colour teal if that needs to be used as a contrast colour.
• Also like teal as a highlight colour.

```html
<!DOCTYPE html>
<html lang="en">
<head>
<meta charset="utf-8">
<title>DM Space Arranging Pty Ltd – Business Card</title>
<link rel="stylesheet" href="https://fonts.googleapis.com/css2?family=Cormorant+Garamond:ital,wght@0,500;0,600;1,500&family=Dancing+Script:wght@500&family=Open+Sans:ital,wght@0,400;1,400&display=swap">
<style>
  :root {
    --backdrop-light: #d4d4d4;
    --backdrop-dark: #8f8f8f;
    --gold-light: #b08a2a;
    --gold-mid: #7f6016;
    --gold-dark: #4e3a0a;
    --band-black: #1c1c1c;
    --band-edge: #3a3a3a;
    --paper-white: #ffffff;
    --paper-shade: #ececec;
    --ink-dark: #1e1e1e;
    --ink-grey: #444444;
    --logo-grey: #8a8a8a;
    --script-white: #f4efe2;
    --script-faint: rgba(255, 248, 230, 0.45);
    --tick-gold: #d9b756;
  }

  * { margin: 0; padding: 0; box-sizing: border-box; }

  html, body {
    width: 1200px;
    height: 871px;
    overflow: hidden;
  }

  body {
    background: radial-gradient(ellipse at 50% 35%, var(--backdrop-light) 0%, var(--backdrop-dark) 100%);
    position: relative;
  }

  .card {
    position: absolute;
    width: 560px;
    height: 320px;
    border-radius: 3px;
    overflow: hidden;
    box-shadow: 0 14px 30px rgba(0, 0, 0, 0.35);
  }

  /* ---------- Reverse side: services ---------- */
  .card-services {
    left: 60px;
    top: 90px;
    background: linear-gradient(160deg, var(--gold-light) 0%, var(--gold-mid) 45%, var(--gold-dark) 100%);
  }

  .tagline {
    position: absolute;
    left: 0;
    width: 100%;
    text-align: center;
    font-family: "Dancing Script", cursive;
    font-weight: 500;
    white-space: nowrap;
  }

  .tagline-top {
    top: 62px;
    font-size: 30px;
    color: var(--script-faint);
  }

  .service-band {
    position: absolute;
    left: 0;
    top: 148px;
    width: 100%;
    height: 112px;
    background: linear-gradient(180deg, var(--band-edge) 0%, var(--band-black) 18%, var(--band-black) 100%);
  }

  .tagline-main {
    top: 118px;
    font-size: 36px;
    color: var(--script-white);
    z-index: 2;
  }

  .service-list {
    position: absolute;
    left: 44px;
    top: 194px;
    width: 500px;
    list-style: none;
    display: grid;
    grid-template-columns: 172px 1fr;
    row-gap: 12px;
    column-gap: 20px;
    font-family: "Open Sans", sans-serif;
    font-size: 12px;
    color: var(--paper-white);
  }

  .service-list li {
    display: flex;
    align-items: center;
    gap: 8px;
    white-space: nowrap;
  }

  .tick { width: 13px; height: 11px; flex: none; }

  /* ---------- Front side: name ---------- */
  .card-name {
    left: 580px;
    top: 450px;
    background: linear-gradient(180deg, var(--paper-white) 0%, var(--paper-white) 60%, var(--paper-shade) 86%);
  }

  .gold-foot {
    position: absolute;
    left: 0;
    bottom: 0;
    width: 100%;
    height: 34px;
    border-top: 4px solid var(--band-black);
    background: linear-gradient(90deg, var(--gold-dark) 0%, var(--gold-light) 50%, var(--gold-mid) 100%);
  }

  .brand {
    position: absolute;
    top: 62px;
    left: 0;
    width: 100%;
    display: flex;
    justify-content: center;
    align-items: center;
    gap: 10px;
  }

  .brand-mark {
    width: 14px;
    height: 14px;
    border-radius: 50%;
    background: var(--logo-grey);
  }

  .brand-name {
    font-family: "Cormorant Garamond", serif;
    font-weight: 600;
    font-size: 17px;
    letter-spacing: 2px;
    text-transform: uppercase;
    color: var(--logo-grey);
    white-space: nowrap;
  }

  .person {
    position: absolute;
    top: 150px;
    left: 0;
    width: 100%;
    text-align: center;
  }

  .person-name {
    font-family: "Cormorant Garamond", serif;
    font-weight: 600;
    font-variant: small-caps;
    font-size: 25px;
    letter-spacing: 1.5px;
    color: var(--ink-dark);
    white-space: nowrap;
  }

  .person-role {
    margin-top: 4px;
    font-family: "Open Sans", sans-serif;
    font-style: italic;
    font-size: 15px;
    color: var(--ink-grey);
  }
</style>
</head>
<body>

  <section class="card card-services">
    <p class="tagline tagline-top">Property Styling</p>
    <div class="service-band"></div>
    <p class="tagline tagline-main">and Cosmetic Renovations</p>
    <ul class="service-list">
      <li><svg class="tick" viewBox="0 0 14 12"><path d="M1 6 L5 10 L13 1" fill="none" stroke="var(--tick-gold)" stroke-width="2.2"/></svg>Staging Houses for Sale</li>
      <li><svg class="tick" viewBox="0 0 14 12"><path d="M1 6 L5 10 L13 1" fill="none" stroke="var(--tick-gold)" stroke-width="2.2"/></svg>Home Styling &amp; Project Management</li>
      <li><svg class="tick" viewBox="0 0 14 12"><path d="M1 6 L5 10 L13 1" fill="none" stroke="var(--tick-gold)" stroke-width="2.2"/></svg>Minor Home Renovations</li>
      <li><svg class="tick" viewBox="0 0 14 12"><path d="M1 6 L5 10 L13 1" fill="none" stroke="var(--tick-gold)" stroke-width="2.2"/></svg>Re-Designing Living Spaces to Aid the Disabled</li>
    </ul>
  </section>

  <section class="card card-name">
    <div class="brand">
      <span class="brand-mark"></span>
      <span class="brand-name">DM Space Arranging Pty Ltd</span>
    </div>
    <div class="person">
      <h1 class="person-name">Marnie Tulloch B.Com LMR HTV</h1>
      <p class="person-role">Property Stylist &amp; Project Manager</p>
    </div>
    <div class="gold-foot"></div>
  </section>

</body>
</html>
```